Business card for Luxury Portable Restroom Trailer company

We are a Luxury Portable Restroom Trailer Company Called FALCRIDGE HIRES. Based in Orange County California. We provide portable restroom trailers for events, such as, Weddings, Concerts, Charity events, Sporting events, Tournaments, Corporate events, ect. We rent and Sell the Luxury restrooms. Our colors are white, grey, and Orange. As you will see in the logo we uploaded.
There are 2 people in the company so the names and titles will change for the 3 people but card will remain the same. Here is the information for each Person: Dwight Penner CFO 555 318-0476
next Person: Leon Marchetti VP 555 318-0476
Next Person: Owen Marchetti CEO 555 318-0476
Information to include on the card: Luxury Restroom Trailers Rental and Sales. Weddings, Concerts, Charity, Sporting and Corp. Events.

```html
<!DOCTYPE html>
<html lang="en">
<head>
<meta charset="utf-8">
<title>Falcridge Hires – Business Card</title>
<link href="https://fonts.googleapis.com/css2?family=Jost:wght@400;500;600&display=swap" rel="stylesheet">
<style>
  :root {
    --orange: #e8621f;
    --charcoal: #3f3f41;
    --card-white: #ffffff;
    --card-grey: #ececec;
    --mark-grey: #d9d9d9;
    --page: #e4e4e4;
  }
  * { box-sizing: border-box; margin: 0; padding: 0; }
  html, body {
    width: 1200px; height: 900px; overflow: hidden;
    background: var(--page);
    font-family: "Jost", "Futura", sans-serif;
    color: var(--charcoal);
  }
  .sheet {
    width: 1200px; height: 900px;
    display: flex; flex-direction: column; align-items: center; justify-content: center;
    gap: 44px;
  }
  .card {
    position: relative;
    width: 640px; height: 366px;
    background: linear-gradient(110deg, var(--card-grey) 0%, #f6f6f6 45%, var(--card-white) 100%);
    box-shadow: 0 6px 18px rgba(0,0,0,.18);
    overflow: hidden;
  }
  .brand-mark {
    position: absolute; top: 38px; right: 44px;
    display: flex; align-items: center; gap: 10px;
    color: var(--orange);
    font-weight: 600; font-size: 30px; letter-spacing: 2px;
  }
  .brand-mark .brand-square {
    width: 18px; height: 18px; background: var(--orange);
  }
  .emblem-watermark {
    position: absolute; left: 40px; top: 90px;
    width: 250px; height: 230px;
    border-radius: 50% 50% 40% 40%;
    background: radial-gradient(ellipse at 55% 45%, var(--mark-grey) 0%, rgba(217,217,217,.6) 50%, rgba(236,236,236,0) 75%);
  }
  .rule {
    position: absolute; left: 0; right: 40px; top: 292px;
    height: 1.5px; background: var(--orange);
  }
  .heading {
    position: absolute; left: 34px; top: 256px;
    color: var(--orange); font-weight: 600;
    font-size: 22px; letter-spacing: .5px; text-transform: uppercase;
  }
  .heading .title {
    color: var(--charcoal); font-weight: 400; text-transform: none;
  }
  .heading .divider { color: var(--orange); font-weight: 400; margin: 0 6px; }
  .services {
    position: absolute; left: 34px; top: 302px; right: 40px;
    font-size: 15.5px; line-height: 1.45; letter-spacing: .3px;
  }
  .services .star { color: var(--orange); margin: 0 4px; }
  .phone {
    position: absolute; left: 34px; top: 306px;
    display: flex; align-items: center; gap: 8px;
    font-size: 17px; letter-spacing: .4px;
  }
</style>
</head>
<body>
<main class="sheet">
  <section class="card card-front">
    <div class="brand-mark"><span class="brand-square"></span>FALCRIDGE HIRES</div>
    <div class="emblem-watermark" role="img" aria-label="Faint oversized brand emblem in light grey"></div>
    <h2 class="heading">Our Services</h2>
    <div class="rule"></div>
    <p class="services">
      Luxury Restroom Trailers Rental and Sales <span class="star">✦</span> Weddings <span class="star">✦</span> Concerts<br>
      Charity <span class="star">✦</span> Sporting and Corp <span class="star">✦</span> Events
    </p>
  </section>

  <section class="card card-back">
    <div class="brand-mark"><span class="brand-square"></span>FALCRIDGE HIRES</div>
    <div class="emblem-watermark" role="img" aria-label="Faint oversized brand emblem in light grey"></div>
    <h1 class="heading">Dwight Penner<span class="divider">|</span><span class="title">CFO</span></h1>
    <div class="rule"></div>
    <p class="phone">
      <svg width="12" height="18" viewBox="0 0 12 18" aria-hidden="true">
        <rect x="1" y="1" width="10" height="16" rx="2" fill="none" stroke="#e8621f" stroke-width="1.5"/>
        <line x1="5" y1="14.5" x2="7" y2="14.5" stroke="#e8621f" stroke-width="1.5"/>
      </svg>
      555 318-0476
    </p>
  </section>
</main>
</body>
</html>
```